Stationery for a private security company, "Brenmoor Security Services Ltd."

Needed is a stationery design for a private security company. The designs must show professionalism and that our company mean nothing but business. Watermark of the company logo on the letterhead page is also a must. The final design must represent innovation and professionalism. It would be great if designers could integrate the colours black and silver onto the cards and letterheads..

Thank you

```html
<!DOCTYPE html>
<html lang="en">
<head>
<meta charset="utf-8">
<title>Brenmoor Security Services Ltd. — Business Cards</title>
<link href="https://fonts.googleapis.com/css2?family=Cinzel:wght@700&family=Arimo:wght@400;700&display=swap" rel="stylesheet">
<style>
  :root {
    --backdrop: #e7e5ea;
    --card: #ffffff;
    --ink: #141414;
    --silver: #8e8e8e;
    --silver-light: #d9d9d9;
    --band: #111111;
    --band-text: #f2f2f2;
    --muted: #555555;
  }
  * { margin: 0; padding: 0; box-sizing: border-box; }
  html, body {
    width: 1200px; height: 934px; overflow: hidden;
    background: var(--backdrop);
  }
  .stationery {
    width: 1200px; height: 934px;
    display: flex; align-items: center; justify-content: center; gap: 60px;
  }
  .card {
    position: relative;
    width: 520px; height: 297px;
    background: var(--card);
    box-shadow: 0 10px 30px rgba(0,0,0,0.12);
    overflow: hidden;
    font-family: 'Arimo', Arial, sans-serif;
    color: var(--ink);
  }
  .brand {
    text-align: center;
    font-family: 'Cinzel', 'Times New Roman', serif;
    font-weight: 700;
    color: var(--ink);
    letter-spacing: 1px;
  }
  .brand-mark {
    display: block;
    width: 14px; height: 14px;
    margin: 0 auto 12px;
    background: var(--silver);
    border-radius: 50%;
  }
  .brand-name { font-size: 34px; line-height: 1; }
  .brand-sub { font-size: 15px; line-height: 1.2; margin-top: 4px; }

  /* Back face */
  .card-back { display: flex; flex-direction: column; align-items: center; justify-content: center; }
  .tagline { margin-top: 20px; font-size: 15px; color: var(--ink); }

  /* Front face */
  .card-front .brand { padding-top: 42px; }
  .holder { text-align: center; margin-top: 26px; }
  .holder-name { font-weight: 700; font-size: 15px; letter-spacing: 0.5px; }
  .holder-role { font-size: 12px; color: var(--muted); margin-top: 3px; }
  .contact-strip {
    position: absolute; left: 0; right: 0; bottom: 0;
    height: 84px;
    border-top: 8px solid var(--silver-light);
    background: var(--band);
    color: var(--band-text);
    font-size: 11.5px; line-height: 1.55;
    text-align: center;
    padding-top: 20px;
  }
  .contact-strip b { font-weight: 700; }
</style>
</head>
<body>
<main class="stationery">
  <section class="card card-back" aria-label="Business card, back">
    <div class="brand">
      <span class="brand-mark"></span>
      <div class="brand-name">BRENMOOR</div>
      <div class="brand-sub">SECURITY SERVICES LTD.</div>
    </div>
    <p class="tagline">A Standard Of Vigilance</p>
  </section>

  <section class="card card-front" aria-label="Business card, front">
    <div class="brand">
      <span class="brand-mark"></span>
      <div class="brand-name">BRENMOOR</div>
      <div class="brand-sub">SECURITY SERVICES LTD.</div>
    </div>
    <div class="holder">
      <div class="holder-name">DILEN MARWAH</div>
      <div class="holder-role">Managing Director</div>
    </div>
    <div class="contact-strip">
      <div>Plot No. 18, Sagar Vihar Soc, Surat - 395011, Gujarat, India</div>
      <div><b>Phone:</b> +91-261-555-0142 · <b>Web:</b> www.brenmoor.com</div>
    </div>
  </section>
</main>
</body>
</html>
```